larkforge website

commerce website to sell cookeries, brackets, mailboxes and to show off homes built. Modern Steel in design see marlo cycles web page to be like: https://www.marlocycles-demo.com/en/ sorry its bright nest hosting word press divi

must be able to add products to page

Target Market(s)

mainly western states of U.S.

Industry/Entity Type

Building Product

Coding

Coded - Design and coding required

Number of Pages Required

3 page

Font styles to use
Sans Serif

Colors

Designer to choose colors to be used in the design.

Requirements
Must have
• customers to be able to order products from page
• bright nest hosting word press divi

```html
<!DOCTYPE html>
<html lang="en">
<head>
<meta charset="utf-8">
<title>Larkforge</title>
<link href="https://fonts.googleapis.com/css2?family=Raleway:wght@500;600;700;800&family=Lato:wght@400;700&display=swap" rel="stylesheet">
<style>
:root{
  --brand:#4b5a88;
  --brand-dark:#3d4a73;
  --ink:#1b1b1b;
  --text:#555;
  --muted:#f3f3f3;
  --topbar:#f6f6f6;
  --white:#fff;
  --star:#f39c12;
  --footer:#1d1d22;
}
*{box-sizing:border-box;margin:0;padding:0}
html,body{width:1200px;height:3607px;overflow:hidden}
body{font-family:"Lato",sans-serif;color:var(--text);background:var(--white);position:relative}
h1,h2,h3,h4{font-family:"Raleway",sans-serif;color:var(--ink)}
a{color:inherit;text-decoration:none}
.accent{color:var(--brand)}
.btn{display:inline-block;background:var(--brand);color:var(--white);font-family:"Raleway",sans-serif;font-weight:700;border-radius:30px;text-align:center}

/* top bar */
.topbar{position:absolute;top:0;left:0;width:1200px;height:43px;background:var(--topbar);font-size:14px;color:#444;display:flex;align-items:center;padding:0 90px}
.topbar .contact{display:flex;gap:18px;align-items:center}
.topbar .contact span{display:flex;align-items:center;gap:6px}
.topbar .right{margin-left:auto;display:flex;align-items:center;gap:14px}
.topbar .sep{width:1px;height:20px;background:#ccc}
.social{width:13px;height:13px;border-radius:50%;background:#555;display:inline-block}

/* nav */
.nav{position:absolute;top:43px;left:0;width:1200px;height:81px;background:var(--brand);display:flex;align-items:center;padding-left:100px}
.brand{color:var(--white);font-family:"Raleway",sans-serif;font-weight:700;font-size:19px;display:flex;align-items:center;gap:8px;width:163px}
.brand i{width:12px;height:12px;border-radius:50%;background:var(--white);display:block}
.menu{display:flex;height:81px}
.menu a{color:var(--white);font-family:"Raleway",sans-serif;font-size:15px;display:flex;align-items:center;padding:0 13px}
.menu a.active{background:#111;padding:0 14px}
.nav-tools{margin-left:auto;margin-right:90px;display:flex;gap:12px;align-items:center}
.circle{width:38px;height:38px;border-radius:50%;background:var(--white);display:flex;align-items:center;justify-content:center}
.cart{height:34px;border-radius:20px;background:var(--white);display:flex;align-items:center;padding:0 14px;gap:8px;font-size:14px;color:#444}

/* hero */
.hero{position:absolute;top:124px;left:0;width:1200px;height:582px;background:radial-gradient(ellipse at 50% 60%,#8a6a55 0%,#5a4a44 40%,#3a3634 75%,#2a2829 100%)}
.hero-copy{position:absolute;top:175px;width:100%;text-align:center;color:var(--white)}
.hero-copy h1{color:var(--white);font-size:56px;font-weight:700;letter-spacing:1px}
.hero-copy p{font-size:21px;font-weight:700;line-height:34px;margin-top:6px}
.hero-copy .btn{margin-top:28px;width:242px;height:70px;line-height:70px;font-size:26px;font-weight:600}
.dots{display:flex;gap:8px;justify-content:center}
.dots i{width:13px;height:13px;border-radius:50%;border:2px solid var(--white);display:block}
.dots i.on{background:var(--white)}
.hero .dots{position:absolute;top:530px;width:100%}

/* about */
.about{position:absolute;top:706px;left:0;width:1200px;height:510px}
.about h2{position:absolute;left:90px;top:88px;font-size:36px;font-weight:700}
.about p,.cookery p{font-size:15.5px;line-height:32px;text-align:justify}
.about p{position:absolute;left:90px;top:144px;width:471px}
.about .btn,.cookery .btn{position:absolute;width:190px;height:50px;line-height:50px;font-size:18px}
.about .btn{left:89px;top:371px}
.framed{position:absolute}
.framed .shadow{position:absolute;background:var(--brand)}
.framed .photo{position:absolute;inset:0;border:1px solid #ccc;background:var(--white)}
.about .framed{left:697px;top:81px;width:395px;height:330px}
.about .framed .shadow{left:16px;top:10px;width:395px;height:330px}
.grill-ph{position:absolute;inset:20px;background:radial-gradient(ellipse at 50% 40%,#bcbcbc 0%,#eee 55%,#fff 100%)}

/* features */
.features{position:absolute;top:1216px;left:0;width:1200px;height:631px;background:var(--muted)}
.features h2{position:absolute;top:56px;width:100%;text-align:center;font-size:40px;font-weight:700}
.cards{position:absolute;top:157px;left:88px;display:flex;gap:19px}
.card{width:241px;height:404px;background:var(--white);box-shadow:0 0 4px rgba(0,0,0,.15);position:relative;overflow:hidden}
.card .pic{height:208px;background:radial-gradient(ellipse at 50% 50%,#6d6d6d 0%,#c9c9c9 45%,#f2f2f2 75%)}
.ribbon{position:absolute;top:-2px;left:-2px;width:0;height:0;border-top:54px solid var(--brand);border-right:54px solid transparent}
.ribbon span{position:absolute;top:-48px;left:2px;transform:rotate(-45deg);color:var(--white);font-size:8px;line-height:8px;width:40px;text-align:center}
.card .body{padding:10px 7px}
.card h3{font-size:19px;font-weight:600;margin-top:2px}
.price{font-size:15px;color:var(--ink);margin-top:10px}
.stars{display:flex;gap:4px;margin-top:8px}
.card p{font-size:12.5px;line-height:21px;margin-top:10px}
.card .actions{display:flex;gap:10px;margin-top:12px}
.pill{height:29px;line-height:29px;border-radius:15px;font-size:11px;font-weight:700;color:var(--white);font-family:"Raleway",sans-serif}
.pill.dark{background:#111;width:88px;text-align:center}
.pill.blue{background:var(--brand);width:117px;text-align:center}
.dots.blue i{border-color:var(--brand);width:11px;height:11px}
.dots.blue i.on{background:var(--brand)}
.features .dots{position:absolute;top:593px;width:100%}

/* cookery */
.cookery{position:absolute;top:1847px;left:0;width:1200px;height:524px}
.cookery .framed{left:90px;top:92px;width:394px;height:330px}
.cookery .framed .shadow{left:16px;top:10px;width:394px;height:330px}
.cookery .framed .photo{border:none;background:radial-gradient(ellipse at 50% 35%,#f4b36b 0%,#d46a2e 18%,#333 40%,#4d7d2a 60%,#2f5a1b 100%)}
.cookery h2{position:absolute;left:637px;top:96px;font-size:36px;font-weight:700}
.cookery p{position:absolute;left:637px;top:150px;width:471px}
.cookery .btn{left:636px;top:373px}

/* testimonials */
.reviews{position:absolute;top:2371px;left:0;width:1200px;height:475px;background:linear-gradient(180deg,#50608e,#47568a)}
.reviews h2{position:absolute;top:58px;width:100%;text-align:center;color:var(--white);font-size:40px;font-weight:700}
.quote{position:absolute;width:306px;background:var(--white);border-radius:12px;padding:20px 24px;font-size:13px;line-height:25px;text-align:justify;color:#666}
.quote::after{content:"";position:absolute;bottom:-10px;left:143px;border-left:10px solid transparent;border-right:10px solid transparent;border-top:10px solid var(--white)}
.who{position:absolute;width:306px;text-align:center;color:var(--white);font-family:"Raleway",sans-serif;font-weight:700;font-size:19px}
.reviews .dots{position:absolute;top:429px;width:100%}
.reviews .dots i{border-color:#111;width:11px;height:11px}
.reviews .dots i.on{background:#111}

/* newsletter */
.newsletter{position:absolute;top:2846px;left:0;width:1200px;height:371px;text-align:center}
.newsletter h2{margin-top:94px;font-size:42px;font-weight:700;color:var(--brand)}
.newsletter p{font-size:22px;color:#333;margin-top:8px}
.signup{position:absolute;left:291px;top:218px;width:623px;height:73px;border:1px solid #333;border-radius:40px;display:flex;align-items:center;padding:4px}
.signup span{flex:1;text-align:left;padding-left:16px;font-size:17px;color:#333}
.signup .btn{width:212px;height:63px;line-height:63px;font-size:22px;border-radius:32px}

/* footer */
.footer{position:absolute;top:3217px;left:0;width:1200px;height:390px;background:radial-gradient(ellipse at 60% 100%,#3a2a22 0%,var(--footer) 55%)}
.footer .brand{position:absolute;left:118px;top:198px;font-size:27px;font-weight:600;width:auto}
.footer .brand i{width:18px;height:18px}
.fcol{position:absolute;top:81px;color:var(--white)}
.fcol h4{color:var(--white);font-size:21px;font-weight:700;margin-bottom:14px}
.fcol li{list-style:none;font-size:15px;line-height:34px;padding-left:5px}
.copyright{position:absolute;left:89px;top:350px;color:var(--white);font-size:15.5px}
.cards-pay{position:absolute;left:826px;top:347px;display:flex;gap:8px}
.cards-pay i{width:41px;height:24px;border-radius:3px;background:#d9d9d9;display:block}
</style>
</head>
<body>

<header class="topbar">
  <div class="contact">
    <span><svg width="13" height="13" viewBox="0 0 24 24"><path fill="#444" d="M6.6 10.8a15 15 0 0 0 6.6 6.6l2.2-2.2a1 1 0 0 1 1-.25 11 11 0 0 0 3.6.6 1 1 0 0 1 1 1V20a1 1 0 0 1-1 1A17 17 0 0 1 3 4a1 1 0 0 1 1-1h3.5a1 1 0 0 1 1 1 11 11 0 0 0 .6 3.6 1 1 0 0 1-.25 1z"/></svg>+888 888 8888</span>
    <span><svg width="14" height="12" viewBox="0 0 24 20"><rect x="1" y="1" width="22" height="18" fill="none" stroke="#444" stroke-width="2"/><path d="M1 2l11 9 11-9" fill="none" stroke="#444" stroke-width="2"/></svg>info@yoursite.com</span>
    <span><svg width="10" height="14" viewBox="0 0 20 28"><path fill="#444" d="M10 0a10 10 0 0 0-10 10c0 7 10 18 10 18s10-11 10-18A10 10 0 0 0 10 0zm0 14a4 4 0 1 1 0-8 4 4 0 0 1 0 8z"/></svg>48 Ember Lane Ridgeview, WI 53990</span>
  </div>
  <div class="right">
    <span>$ USD &#8964;</span><span class="sep"></span>
    <i class="social"></i><i class="social"></i><i class="social"></i>
  </div>
</header>

<nav class="nav">
  <a class="brand" href="#"><i></i>LARKFORGE</a>
  <div class="menu">
    <a class="active" href="#">HOME</a><a href="#">ABOUT</a><a href="#">SHOP</a><a href="#">FIREPIT COOKERY</a><a href="#">BLOG</a><a href="#">CONTACT US</a>
  </div>
  <div class="nav-tools">
    <span class="circle"><svg width="14" height="14" viewBox="0 0 24 24"><circle cx="10" cy="10" r="7" fill="none" stroke="#333" stroke-width="3"/><path d="M15 15l6 6" stroke="#333" stroke-width="3"/></svg></span>
    <span class="circle"><svg width="13" height="14" viewBox="0 0 24 26"><circle cx="12" cy="7" r="6" fill="#333"/><path d="M0 26a12 10 0 0 1 24 0z" fill="#333"/></svg></span>
    <span class="cart"><svg width="15" height="13" viewBox="0 0 24 20"><path d="M2 7h20l-2 13H4z" fill="#333"/><path d="M7 7a5 5 0 0 1 10 0" fill="none" stroke="#333" stroke-width="2"/></svg>3 <span style="width:1px;height:18px;background:#bbb"></span>$50.00</span>
  </div>
</nav>

<section class="hero" role="img" aria-label="Meat grilling over open flames on a steel grate">
  <div class="hero-copy">
    <h1>LARKFORGE</h1>
    <p>Sed ut perspiciatis unde omnis iste natus error sit voluptatem accusantium<br>doloremque laudantium, totaam rem aperiam</p>
    <a class="btn" href="#">SHOP NOW</a>
  </div>
  <div class="dots"><i class="on"></i><i></i><i class="on"></i></div>
</section>

<section class="about">
  <h2>ABOUT US <span class="accent">LARKFORGE</span></h2>
  <p>Sed ut perspiciatis unde omnis iste natus error sit voluptatem accusantium doloremque laudantium, totam rem aperiam, eaque ipsa quae ab illo inventore veritatis et quasi architecto beatae vitae dicta sunt explicabo. Nemo enim ipsam voluptatem quia voluptas sit aspernatur aut odit aut fugit, sed quia consequuntur magni dolores eos qui ratione voluptatem</p>
  <a class="btn" href="#">READ MORE</a>
  <div class="framed">
    <div class="shadow"></div>
    <div class="photo"><div class="grill-ph" role="img" aria-label="Firepit cooker on a tripod stand with side trays and meat on the pan"></div></div>
  </div>
</section>

<section class="features">
  <h2>FEATURES <span class="accent">PRODUCTS</span></h2>
  <div class="cards">
    <article class="card">
      <div class="pic" role="img" aria-label="Black fire bowl on a steel stand"></div>
      <div class="ribbon"><span>PRICE DROP</span></div>
      <div class="body">
        <h3>FINIBUS BONORUM</h3><div class="price">$35.00</div>
        <div class="stars"><svg width="84" height="14" viewBox="0 0 84 14"><g fill="#f39c12"><path id="st" d="M7 0l2 5h5l-4 3 1.6 5L7 10l-4.6 3L4 8 0 5h5z"/><use href="#st" x="17"/><use href="#st" x="34"/><use href="#st" x="51"/><use href="#st" x="68"/></g></svg></div>
        <p>Sed ut perspiciatis unde omnis iste natus error sit voluptatem</p>
        <div class="actions"><span class="pill dark">ADD TO CART</span><span class="pill blue">ADD TO COMPARE</span></div>
      </div>
    </article>
    <article class="card">
      <div class="pic" role="img" aria-label="Stainless gas grill with side burners"></div>
      <div class="ribbon"><span>OUT OF STOCK</span></div>
      <div class="body">
        <h3>BONORUM</h3><div class="price">$45.00</div>
        <div class="stars"><svg width="84" height="14" viewBox="0 0 84 14"><g fill="#f39c12"><use href="#st"/><use href="#st" x="17"/><use href="#st" x="34"/><use href="#st" x="51"/><use href="#st" x="68"/></g></svg></div>
        <p>Sed ut perspiciatis unde omnis iste natus error sit voluptatem</p>
        <div class="actions"><span class="pill dark">ADD TO CART</span><span class="pill blue">ADD TO COMPARE</span></div>
      </div>
    </article>
    <article class="card">
      <div class="pic" role="img" aria-label="Round kettle grill on wheeled legs"></div>
      <div class="ribbon"><span>NEW OFFER</span></div>
      <div class="body">
        <h3>FINIBUS</h3><div class="price">$50.00</div>
        <div class="stars"><svg width="84" height="14" viewBox="0 0 84 14"><g fill="#f39c12"><use href="#st"/><use href="#st" x="17"/><use href="#st" x="34"/><use href="#st" x="51"/><use href="#st" x="68"/></g></svg></div>
        <p>Sed ut perspiciatis unde omnis iste natus error sit voluptatem</p>
        <div class="actions"><span class="pill dark">ADD TO CART</span><span class="pill blue">ADD TO COMPARE</span></div>
      </div>
    </article>
    <article class="card">
      <div class="pic" role="img" aria-label="Charcoal barrel grill with wooden side shelf"></div>
      <div class="ribbon"><span>NEW SALE</span></div>
      <div class="body">
        <h3>LOREM IPSUM</h3><div class="price">$55.00</div>
        <div class="stars"><svg width="84" height="14" viewBox="0 0 84 14"><g fill="#f39c12"><use href="#st"/><use href="#st" x="17"/><use href="#st" x="34"/><use href="#st" x="51"/><use href="#st" x="68"/></g></svg></div>
        <p>Sed ut perspiciatis unde omnis iste natus error sit voluptatem</p>
        <div class="actions"><span class="pill dark">ADD TO CART</span><span class="pill blue">ADD TO COMPARE</span></div>
      </div>
    </article>
  </div>
  <div class="dots blue"><i class="on"></i><i></i><i class="on"></i></div>
</section>

<section class="cookery">
  <div class="framed">
    <div class="shadow"></div>
    <div class="photo" role="img" aria-label="Kettle grill with flames rising from the grate on a lawn"></div>
  </div>
  <h2>COOKERY <span class="accent">MANUFACTURER.</span></h2>
  <p>Sed ut perspiciatis unde omnis iste natus error sit voluptatem accusantium doloremque laudantium, totam rem aperiam, eaque ipsa quae ab illo inventore veritatis et quasi architecto beatae vitae dicta sunt explicabo. Nemo enim ipsam voluptatem quia voluptas sit aspernatur aut odit aut fugit, sed quia consequuntur magni dolores eos qui ratione voluptatem</p>
  <a class="btn" href="#">READ MORE</a>
</section>

<section class="reviews">
  <h2>OUR SATISFIED CUSTOMERS</h2>
  <blockquote class="quote" style="left:90px;top:201px">Lorem ipsum dolor sit amet, consectetur adipiscing elit, sed do eiusmod tempor incididunt ut labore et dolore magna aliqua. Ut enim ad minim veniam, quis nostrud exercitation ullamco laboris nisi ut aliquip ex ea commodo reprehenderit</blockquote>
  <div class="who" style="left:90px;top:408px">JAMES</div>
  <blockquote class="quote" style="left:447px;top:138px">Lorem ipsum dolor sit amet, consectetur adipiscing elit, sed do eiusmod tempor incididunt ut labore et dolore magna aliqua. Ut enim ad minim veniam, quis nostrud exercitation ullamco laboris nisi ut aliquip ex ea commodo reprehenderit</blockquote>
  <div class="who" style="left:447px;top:345px">SMITH</div>
  <blockquote class="quote" style="left:799px;top:201px">Lorem ipsum dolor sit amet, consectetur adipiscing elit, sed do eiusmod tempor incididunt ut labore et dolore magna aliqua. Ut enim ad minim veniam, quis nostrud exercitation ullamco laboris nisi ut aliquip ex ea commodo reprehenderit</blockquote>
  <div class="who" style="left:799px;top:405px">WILLAMSON</div>
  <div class="dots"><i></i><i class="on"></i><i></i></div>
</section>

<section class="newsletter">
  <h2>NEWSLETTER</h2>
  <p>Register now to get updates on promotions and coupons.</p>
  <div class="signup"><span>Enter the email</span><a class="btn" href="#">SUBSCRIBE</a></div>
</section>

<footer class="footer">
  <a class="brand" href="#"><i></i>LARKFORGE</a>
  <div class="fcol" style="left:364px"><h4>QUICKS LINKS</h4><ul><li>Home</li><li>About</li><li>Shop</li><li>Firepit Cookery</li><li>Blog</li><li>Contact Us</li></ul></div>
  <div class="fcol" style="left:561px"><h4>OTHER LINKS</h4><ul><li>Create an Account</li><li>Making Payments</li><li>Delivery Options</li><li>Buyer Protection</li><li>Terms and conditions</li></ul></div>
  <div class="fcol" style="left:758px"><h4>OTHER LINKS</h4><ul><li>My Account</li><li>Wish List</li><li>Order History</li><li>Brands</li><li>Newsletter</li></ul></div>
  <div class="fcol" style="left:930px"><h4>CONTACT US</h4><ul><li>48 Ember Lane</li><li>Ridgeview, WI 53990</li><li>+888 888 8888</li><li>info@yoursite.com</li></ul></div>
  <div class="copyright">© Copyright 2020 Larkforge. All rights reserved.</div>
  <div class="cards-pay"><i></i><i></i><i></i><i></i><i></i><i></i></div>
</footer>

</body>
</html>
```